Business Card Design Project

The business card is for an educational company that provides personalised tuition to students.

The company logo is in orange and blue (as provided) and should be included in the name card design

The philosophy of the company is to make learning a comfortable experience for student as such design of the namecard should look fresh and has a bit of the 'wow' factor. Some of the namecard design that appeals to me are as uploaded under Sample Design.

The particulars that need to be provided are:
(1): Company Name (Lantern Education)
(1): Name
(2): Educational qualifications which will appear below name
(3): Mobile number
(4): Email address
(5): Website

Industry/Entity Type

Business

Requirements
Must have
• (1): Company Logo

(2): The card background should preferably be coloured both for the front side and back.

(3): The choice of font is important as part of the selection consideration. There is no preferred font that I have selected, designer is free to choose the font that will complement their design.

```html
<!DOCTYPE html>
<html lang="en">
<head>
<meta charset="utf-8">
<title>Lantern Education – Business Card</title>
<link rel="stylesheet" href="https://fonts.googleapis.com/css2?family=Overlock:wght@400;700&display=swap">
<style>
  :root {
    --page-bg: #e6e6e6;
    --brand-orange: #ef7022;
    --brand-blue: #2f9bd8;
    --card-white: #ffffff;
    --logo-grey: #4a4a4a;
    --divider-grey: #c9c9c9;
    --card-shadow: rgba(0, 0, 0, 0.18);
  }
  * { box-sizing: border-box; margin: 0; padding: 0; }
  html, body {
    width: 1200px;
    height: 900px;
    overflow: hidden;
    background: var(--page-bg);
  }
  .sheet {
    position: relative;
    width: 1200px;
    height: 900px;
  }
  .card {
    position: absolute;
    left: 250px;
    width: 700px;
    height: 400px;
    overflow: hidden;
    box-shadow: 0 6px 18px var(--card-shadow);
  }
  .card--back {
    top: 35px;
    background: var(--brand-orange);
  }
  .card--front {
    top: 465px;
    background: var(--card-white);
  }

  /* Brand lockup */
  .brand {
    position: absolute;
    display: flex;
    align-items: center;
  }
  .brand__mark {
    flex: none;
    border-radius: 8px;
    background: var(--brand-blue);
  }
  .brand__name {
    font-family: 'Overlock', 'Trebuchet MS', sans-serif;
    font-weight: 700;
    line-height: 1.0;
  }
  .card--back .brand {
    left: 60px;
    top: 125px;
    gap: 26px;
  }
  .card--back .brand__mark {
    width: 120px;
    height: 120px;
    border-radius: 16px;
  }
  .card--back .brand__name {
    color: var(--card-white);
    font-size: 58px;
  }
  .card--front .brand {
    left: 66px;
    top: 150px;
    gap: 14px;
  }
  .card--front .brand__mark {
    width: 56px;
    height: 56px;
  }
  .card--front .brand__name {
    color: var(--logo-grey);
    font-size: 29px;
  }

  /* Divider */
  .card__divider {
    position: absolute;
    left: 330px;
    top: 95px;
    width: 1px;
    height: 195px;
    background: var(--divider-grey);
  }

  /* Contact column */
  .contact {
    position: absolute;
    left: 358px;
    top: 72px;
    font-family: 'Overlock', 'Trebuchet MS', sans-serif;
  }
  .contact__name {
    color: var(--brand-blue);
    font-size: 30px;
    font-weight: 700;
    letter-spacing: 0.5px;
    line-height: 1;
  }
  .contact__role {
    color: var(--brand-orange);
    font-size: 19px;
    margin: 2px 0 0 14px;
  }
  .contact__phones {
    margin-top: 38px;
    color: var(--brand-orange);
    font-size: 19px;
    line-height: 1.35;
  }
  .contact__web {
    margin-top: 22px;
    color: var(--brand-blue);
    font-size: 19px;
    line-height: 1.35;
  }

  /* Bottom band */
  .card__band {
    position: absolute;
    left: 0;
    bottom: 0;
    width: 700px;
    height: 24px;
    display: block;
  }
</style>
</head>
<body>
<main class="sheet">

  <section class="card card--back" aria-label="Business card, back">
    <div class="brand">
      <span class="brand__mark" aria-hidden="true"></span>
      <span class="brand__name">Lantern<br>Education</span>
    </div>
  </section>

  <section class="card card--front" aria-label="Business card, front">
    <div class="brand">
      <span class="brand__mark" aria-hidden="true"></span>
      <span class="brand__name">Lantern<br>Education</span>
    </div>

    <div class="card__divider" aria-hidden="true"></div>

    <div class="contact">
      <p class="contact__name">JOHN DOE</p>
      <p class="contact__role">General manager</p>
      <div class="contact__phones">
        <p>Phone: 415 907 2638</p>
        <p>Mobile: 86402917</p>
      </div>
      <div class="contact__web">
        <p>info@lanterneducation.com</p>
        <p>www.lanterneducation.com</p>
      </div>
    </div>

    <svg class="card__band" viewBox="0 0 700 24" aria-hidden="true">
      <polygon points="0,0 545,0 520,24 0,24" fill="var(--brand-orange)"/>
      <polygon points="549,0 700,0 700,24 524,24" fill="var(--brand-blue)"/>
    </svg>
  </section>

</main>
</body>
</html>
```